Enlighted Feel-Good Wrapper Design for Cannabis Snack Bar: Vesko Bites.

We need a logo and wrapper for the first product in our line-up, Pip Crackle Maple! - Honey Salted Nuts and Dark Chocolate. Please highlight the name Maple Pip Crackle!, more than the name Vesko Bites or flavor of the bar. The package dimensions unfolded and unsealed are 6.5 inches x 5.25 inches. I have uploaded 3 photos of similar bar wrappers as an example of the wrapper type. The winning design will be awarded an extra amount for the Vesko Bites logo from Craft Hive.

It is a nut based snack bar similar to brands like Brisk, Stellar Munch, Orla, and Rover Bars. The difference is that this bar will contain THC and/or CBD oils. It is designed for the Medical Marijuana market in California. I would like the bar to be more upscale in design as we are going after a demographic with a higher disposable income and will be in their 30's-60's. We would like the brand to be appealing to both men and women. We would like the wrapper/logo to have an air of enlightenment to it. We want people to feel like they will be at peace when they eat this bar. Please do not make the design flashy, or decorated with marijuana leaves. We do not want something cheesy. We uploaded pictures of the bar so you can see what they look like. The packaging has to be OPAQUE.

Please include all the following. If you don't know specific values, weights or ingredients please fill the space with any text that can be substituted.

Label Regulatory Requirements:

(1) The identity of the product in a text size reasonably related to the most prominent printed matter on the panel;
(2) The words “cannabis-infused” immediately above the identity of the product in bold type and a text size larger than the text size used for the identity of the product;
(3) The cannabis product symbol uploaded in this post. The symbol shall be no smaller in size than half (.5) inch by half (.5) inch and shall be printed legibly and conspicuously;
(4) The net weight or volume of the contents of the package;

1.4 oz (40g)

(5) The THC content and CBD content for the package in its entirety, expressed in milligrams per package;

40mg

(6) The THC content and CBD content per serving, expressed in milligrams per serving;

10mg

(b) The primary panel text must be in type size no less than 6 point font and be in relation to the size of the primary panel and container.

40408. Informational Panel Labeling Requirements.
(a) The label for a medical cannabis product shall include an informational panel that includes the following:
(1) The licensed manufacturer and its contact number or website address;

Vesko Bites, San Diego, CA (555)302-7194, www.veskobites.example

(2) The date of manufacture;
(3) Each of the following statements:
(A) “SCHEDULE I CONTROLLED SUBSTANCE.”
(B) “KEEP OUT OF REACH OF CHILDREN AND ANIMALS” in bold print.
(C) “FOR MEDICAL USE ONLY.”
(D) “IF PREGNANT OR BREASTFEEDING, CONSULT A PHYSICIAN PRIOR TO USE.”
(E) “THE INTOXICATING EFFECTS OF THIS PRODUCT MAY BE DELAYED BY UP TO TWO HOURS.”
(F) “THIS PRODUCT MAY IMPAIR THE ABILITY TO DRIVE OR OPERATE MACHINERY, PLEASE USE EXTREME CAUTION.”
(4) A list of all product ingredients in descending order of predominance by weight or volume;

NUT MIXTURE:
almonds, peanuts, walnuts, puffed rice, flaxseed

SYRUP:
honey, brown rice syrup, sea salt, vanilla

CHOCOLATE DRIZZLE:
dark chocolate, coconut oil

(5) If an edible product that contains an ingredient, flavoring, coloring, or an incidental additive that bears or contains a major food allergen, the word “contains,” followed by a list of the applicable major food allergens;

Contains tree nuts.

(6) If an edible product, the names of any artificial food colorings contained in the product;
(7) If an edible product, the amount, in grams, of sodium, sugar, carbohydrates, and total fat per serving;

Dark Chocolate Sea Salt: 193 calories, 12.5g fat, 95mg sodium, 18.9g carbs, 2.1g fiber, 14g sugars, 5.2g protein

(8) The lot number;
(9) Instructions for use, such as the method of consumption or application, and any preparation necessary prior to use;
(10) The product expiration date, “use by” date, or “best by” date; and
(11) The unique identifier.
(b) The informational panel text shall be in a type size of no less than 6 point font and in relation to the size of the primary panel and container, unless there is insufficient area on the container available to print all the required information in a type size of no less than 6 point font. In such a case, the label shall include the warning statements required by paragraph (3) in a type size of no less than 6 point font, and the product shall be accompanied by a supplemental labeling that includes all of the information required by this section. The text of the supplemental labeling shall be no less than 8 point font.

The label shall not contain any of the following:

(a) Claims that the manufactured cannabis or cannabis product was grown in a California county when the cannabis was not grown there.
(b) The name of a California county unless the cannabis was grown there.
(c) Content that is or designed to be attractive to individuals under the age of 21, including but not limited to:
(1) Cartoons;
(2) Any likeness to images, characters, or phrases that are popularly used to advertise to children; or
(3) Any imitation of candy packaging or labeling.
(d) False labeling information. Labeling is false if it is false or misleading in any particular.
(e) Claims of health benefits or other physical benefits.
Updates

Industry/Entity Type

Retail

Logo Text

Vesko Bites

Colors

Designer to choose colors to be used in the design.

Requirements
Must have
• I would like to have a logo/icon of an cute owl or icon of a small tree branch with leaves and nut hanging off or anything else that you think would be a good logo incorporated with the company name "Vesko Bites." I uploaded a logo of an owl logo that I like. Feel free to adjust and create something creative, please do not copy it.
• The wrapper needs to reflect an upscale, natural, farm fresh, whole food product. We are trying to build a high end line of products that appeal to health conscious women and men ages 30 - 60 years old.
• Please include text from Allergen warning in one of the uploaded photos.
• Please add - "Gluten free" to the label, "Non GMO" or "GMO Free" and "No Soy" or "Soy Free", and "Dairy Free" as either writing or as an icon of some sort.
Nice to have
• Please see posted photos of some wrappers of food products that I like for ideas. Some color suggestions to incorporate: Red, Yellow, Green, Orange simply because these colors have been proven appealing to the eye for food labels. You may use one or a few of these and can balance them out with other colors. Please do not use traditional colors associated with cannabis such as dark brown or deep green. Subdued, natural looking versions of these may be okay if they are balanced out with other colors or the rest of the bar. I would also like the wrapper to have some graphics that can illustrate what the bar actually looks like so that people know whats inside!
• The final design should communicate:
• Freshness
• Organic
• Healthy
• Modern
Should not have
• I do not want this product to have graphics of typical cheesy cannabis/marijuana leaves or any other low class graphics related to the industry. Not graphics of marijuana flower, joints, smoke or leaves.

```html
<!DOCTYPE html>
<html lang="en">
<head>
<meta charset="utf-8">
<title>Vesko Bites – Maple Pip Crackle! Bar Wrapper</title>
<link rel="stylesheet" href="https://fonts.googleapis.com/css2?family=Libre+Baskerville:wght@400;700&family=Open+Sans+Condensed:wght@300&family=Open+Sans:wght@400&display=swap">
<style>
  :root {
    --backdrop: #969696;
    --page: #fefefe;
    --wrapper-white: #f4f4f4;
    --crimp-red: #c8202a;
    --band-amber: #c6842d;
    --ink-brown: #3a1e14;
    --text-white: #ffffff;
    --warning-blue: #2ea6d8;
    --bar-dark: #4a2a1c;
    --bar-light: #d9c48f;
  }
  html, body {
    margin: 0;
    padding: 0;
    width: 1200px;
    height: 1200px;
    overflow: hidden;
    background: var(--page);
  }
  .canvas {
    position: relative;
    width: 1200px;
    height: 1200px;
  }
  .backdrop {
    position: absolute;
    left: 0; top: 30px;
    width: 1200px; height: 506px;
    background: var(--backdrop);
  }
  .wrapper {
    position: absolute;
    left: 0; top: 0;
    width: 1200px; height: 1200px;
  }
  .serif { font-family: 'Libre Baskerville', Georgia, serif; }
  .sans { font-family: 'Open Sans Condensed', 'Open Sans', Arial, sans-serif; }
</style>
</head>
<body>
<main class="canvas">
  <div class="backdrop"></div>

  <svg class="wrapper" viewBox="0 0 1200 1200" xmlns="http://www.w3.org/2000/svg">
    <!-- wrapper body -->
    <rect class="wrapper-body" x="90" y="98" width="1014" height="372" fill="var(--wrapper-white)"/>

    <!-- product view of the bar -->
    <rect class="bar-view" x="160" y="132" width="904" height="118" fill="url(#barTones)" role="img" aria-label="Nut bar with almonds, peanuts and puffed rice drizzled with dark chocolate"/>
    <defs>
      <linearGradient id="barTones" x1="0" y1="0" x2="1" y2="0">
        <stop offset="0" stop-color="var(--bar-light)"/>
        <stop offset="0.5" stop-color="#a8794a"/>
        <stop offset="1" stop-color="var(--bar-light)"/>
      </linearGradient>
    </defs>

    <!-- amber flavour band -->
    <path class="flavour-band" d="M160 248 C 320 236, 520 252, 700 244 C 860 238, 980 252, 1064 250 L 1064 456 C 900 444, 700 440, 500 442 C 340 444, 220 450, 160 454 Z" fill="var(--band-amber)"/>

    <!-- red crimp on the left -->
    <rect class="crimp-left" x="90" y="98" width="70" height="372" fill="var(--crimp-red)"/>
    <!-- white crimp on the right -->
    <rect class="crimp-right" x="1060" y="98" width="44" height="372" fill="#ebebeb"/>

    <!-- brand triangle -->
    <polygon class="brand-triangle" points="312,148 174,402 450,398" fill="var(--text-white)"/>
    <polygon class="infused-flag" points="176,170 300,170 232,276" fill="var(--crimp-red)"/>
    <text class="serif" x="238" y="193" font-size="12.5" font-weight="700" fill="var(--text-white)" text-anchor="middle">CANNABIS</text>
    <text class="serif" x="238" y="206" font-size="12.5" font-weight="700" fill="var(--text-white)" text-anchor="middle">INFUSED</text>

    <text class="sans" x="181" y="292" font-size="26" fill="var(--ink-brown)">40g</text>

    <!-- brand name -->
    <circle class="brand-dot" cx="312" cy="288" r="9" fill="var(--band-amber)"/>
    <text class="serif brand-name" x="312" y="336" font-size="30" fill="var(--ink-brown)" text-anchor="middle">Vesko</text>
    <text class="serif brand-name" x="312" y="374" font-size="30" fill="var(--ink-brown)" text-anchor="middle">Bites</text>

    <!-- product name -->
    <text class="serif product-name" x="414" y="312" font-size="41" font-weight="700" fill="var(--text-white)" letter-spacing="1">MAPLE PIP CRACKLE!</text>
    <text class="serif" x="966" y="304" font-size="18" font-weight="700" fill="var(--text-white)" letter-spacing="2">BAR</text>
    <text class="serif flavour" x="436" y="348" font-size="24" font-weight="700" fill="var(--text-white)">SALTED DARK CHOCOLATE &amp; NUTS</text>
    <text class="serif claims" x="480" y="375" font-size="14" font-weight="700" fill="var(--ink-brown)">• NON-GMO • GLUTEN-FREE • NO SOY • DAIRY-FREE</text>

    <!-- cannabinoid content -->
    <text class="sans" x="870" y="403" font-size="13" fill="var(--ink-brown)">THC content 40mg/pack</text>
    <text class="sans" x="870" y="417" font-size="13" fill="var(--ink-brown)">CBD content 10mg/serving</text>

    <!-- cannabis product symbol area -->
    <polygon class="product-symbol" points="932,187 1022,187 977,261" fill="var(--crimp-red)" stroke="var(--warning-blue)" stroke-width="3"/>
  </svg>
</main>
</body>
</html>
```